Antibacterial Hand Wash Squeeze Tube Label

We're looking for a contemporary label design for a new Antibacterial Hand Wash for an 8oz squeeze tube. The new consumer brand will be sold to consumers in major US retail stores & online. The moisturizing hand wash contains Aloe Vera, vitamin E, and other natural ingredients so the design should include the color green. Real photos are very effective on packaging, so a picture of Aloe Vera or possibly two hands washing would help draw consumers' attention to the tube on the retail shelf. The front label may wrap around the sides. Rear must be left mostly blank
Target Market(s)
US Consumers - retail stores & online
Industry/Entity Type
Consumer

```html
<!DOCTYPE html>
<html lang="en">
<head>
<meta charset="utf-8">
<title>Aloe Vera Hand Wash Label</title>
<link href="https://fonts.googleapis.com/css2?family=Arimo:wght@700&display=swap" rel="stylesheet">
<style>
  :root {
    --ink: #137a00;
    --band-start: #8cff1a;
    --band-end: #c6ff7a;
    --pill-start: #62ff00;
    --pill-end: #dcff8e;
    --leaf-deep: #2f9e0c;
    --leaf-mid: #62d21c;
    --leaf-light: #a9f060;
    --haze: #eafde2;
    --paper: #ffffff;
  }
  html, body {
    margin: 0;
    padding: 0;
    width: 1067px;
    height: 1200px;
    overflow: hidden;
    background: var(--paper);
  }
  .label {
    position: relative;
    width: 1067px;
    height: 1200px;
    background: var(--paper);
    font-family: "Arimo", Arial, sans-serif;
    font-weight: 700;
    color: var(--ink);
  }
  .title-band {
    position: absolute;
    left: 0;
    top: 46px;
    width: 1067px;
    height: 177px;
    background: linear-gradient(90deg, var(--band-start), var(--band-end));
  }
  .product-name {
    position: absolute;
    left: 0;
    top: 28px;
    width: 530px;
    margin: 0;
    text-align: center;
    font-size: 60px;
    line-height: 62px;
    letter-spacing: -0.5px;
  }
  .aloe-photo {
    position: absolute;
    left: 0;
    top: 223px;
    width: 1067px;
    height: 933px;
    background:
      radial-gradient(ellipse 230px 520px at 260px 520px, var(--leaf-deep) 0%, var(--leaf-mid) 55%, rgba(98,210,28,0) 100%),
      radial-gradient(ellipse 420px 700px at 180px 700px, var(--leaf-mid) 0%, rgba(169,240,96,0.6) 60%, rgba(169,240,96,0) 100%),
      linear-gradient(90deg, var(--leaf-light) 0%, #d6f9bd 55%, var(--haze) 100%);
  }
  .feature {
    position: absolute;
    left: 0;
    height: 62px;
    border-radius: 0 12px 12px 0;
    background: linear-gradient(90deg, var(--pill-start), var(--pill-end));
    font-size: 34px;
    line-height: 62px;
    white-space: nowrap;
    box-sizing: border-box;
  }
  .feature--vitamin { top: 498px; width: 228px; padding-left: 33px; }
  .feature--moist { top: 605px; width: 239px; padding-left: 30px; }
  .feature--antibac { top: 712px; width: 255px; padding-left: 24px; }
  .feature--natural { top: 826px; width: 443px; padding-left: 21px; }
  .net-volume {
    position: absolute;
    left: 268px;
    top: 1058px;
    font-size: 31px;
    line-height: 36px;
  }
</style>
</head>
<body>
  <div class="label">
    <div class="title-band">
      <h1 class="product-name">Aloe Vera<br>Hand Wash</h1>
    </div>
    <div class="aloe-photo" role="img" aria-label="Close-up photograph of green aloe vera leaves against a soft pale background"></div>
    <div class="feature feature--vitamin">Vitamin E</div>
    <div class="feature feature--moist">Moisturizing</div>
    <div class="feature feature--antibac">Anti-Bacterial</div>
    <div class="feature feature--natural">Other Natural Ingredients</div>
    <div class="net-volume">8oz (236ml)</div>
  </div>
</body>
</html>
```